Norrell Advisory WA Business Card

Create an interesting, eye catching and colourful two sided business card. We are a business consulting operation assisting SME's improve all areas of their business. We provide consulting services to assist SME's to create a culture of continuous improvement, making a positive difference in the business. Our tag line is Small changes, big rewards. We want to create a well recognised, innovative brand that can be continued throughout our website, social media and email correspondence.

Target Market(s)

Small to Medium Enterprise Business Owners

Industry/Entity Type

Business Consultant

Contact Information for Business Card

Name of Business: Norrell Advisory - Steady Steps Lasting Gains
Derek Holloway Ph 0407385510 Megan Holloway Ph 0407913847
Email norrelladvisorywa@mailbox-example.com
Web address TBA
FaceBook page TBA

BACKSIDE OF CARD

Providing assistance with:

• Organisation & Efficiency
• Revenue generation & Marketing
• Financial Management
• Production quality & delivery
• Systems & Process documentation
• Exit Strategy

Font styles to use
Other font styles liked:
• Calibri

Colors

Designer to choose colors to be used in the design.

Requirements
Must have
• Calibri font

```html
<!DOCTYPE html>
<html lang="en">
<head>
<meta charset="utf-8">
<title>Norrell Advisory WA Business Card</title>
<link rel="stylesheet" href="https://fonts.googleapis.com/css2?family=Carlito:ital,wght@0,400;0,700;1,700&family=Open+Sans:wght@600;700&display=swap">
<style>
  :root {
    --canvas: #e6e6e6;
    --panel-dark: #2f2f2f;
    --name-blue: #1a7ac0;
    --white: #ffffff;
    --ink: #2e2e2e;
    --ink-soft: #555555;
    --blue-light: #3a9ed6;
    --blue-deep: #0a6fb4;
    --pattern-a: #eef5fb;
    --pattern-b: #fdf7ea;
    --pattern-c: #f7eef0;
  }
  * { margin: 0; padding: 0; box-sizing: border-box; }
  html, body {
    width: 1125px;
    height: 1200px;
    overflow: hidden;
    background: var(--canvas);
    font-family: "Carlito", Calibri, sans-serif;
  }
  .card {
    position: absolute;
    left: 157px;
    width: 826px;
    height: 472px;
    overflow: hidden;
  }
  .card--front { top: 106px; display: flex; }
  .card--back {
    top: 639px;
    background: radial-gradient(ellipse at 50% 40%, var(--blue-light) 0%, var(--blue-deep) 85%);
    color: var(--white);
  }

  /* Front: contact panel */
  .contact-panel {
    width: 385px;
    height: 100%;
    background: var(--panel-dark);
    color: var(--white);
    padding: 122px 0 0 42px;
  }
  .person { margin-bottom: 14px; }
  .person__name {
    font-family: "Open Sans", sans-serif;
    font-weight: 600;
    font-size: 27px;
    line-height: 30px;
    color: var(--name-blue);
    white-space: nowrap;
  }
  .person__phone {
    font-family: "Open Sans", sans-serif;
    font-weight: 700;
    font-size: 16px;
    line-height: 22px;
  }
  .links { list-style: none; margin-top: 14px; }
  .links__item {
    display: flex;
    align-items: center;
    gap: 11px;
    font-size: 17px;
    line-height: 25px;
    white-space: nowrap;
  }
  .links__icon { width: 16px; height: 16px; flex: none; }

  /* Front: brand panel */
  .brand-panel {
    position: relative;
    flex: 1;
    height: 100%;
  }
  .brand-panel__backdrop {
    position: absolute;
    inset: 0;
    background:
      radial-gradient(circle at 20% 25%, var(--pattern-c) 0, transparent 35%),
      radial-gradient(circle at 80% 75%, var(--pattern-b) 0, transparent 40%),
      linear-gradient(135deg, var(--pattern-a), var(--pattern-b) 50%, var(--pattern-a));
  }
  .brand {
    position: absolute;
    left: 0; right: 0;
    top: 178px;
    text-align: center;
  }
  .brand__mark {
    display: inline-block;
    width: 30px; height: 30px;
    background: var(--name-blue);
    margin-bottom: 14px;
  }
  .brand__name {
    font-weight: 700;
    font-size: 31px;
    line-height: 34px;
    color: var(--ink);
    letter-spacing: 0.5px;
    text-transform: uppercase;
  }
  .brand__tagline {
    font-size: 18px;
    line-height: 22px;
    color: var(--ink-soft);
    letter-spacing: 2px;
    text-transform: uppercase;
  }

  /* Back */
  .back-brand {
    position: absolute;
    left: 0; right: 0;
    top: 150px;
    text-align: center;
  }
  .back-brand__mark {
    display: inline-block;
    width: 44px; height: 44px;
    background: var(--white);
    margin-bottom: 16px;
  }
  .back-brand__name {
    font-weight: 700;
    font-size: 40px;
    line-height: 44px;
    color: var(--white);
  }
  .services {
    position: absolute;
    left: 62px; right: 62px;
    top: 336px;
    text-align: center;
  }
  .services__heading {
    display: flex;
    align-items: center;
    gap: 6px;
    font-weight: 700;
    font-style: italic;
    font-size: 27px;
    line-height: 32px;
    white-space: nowrap;
  }
  .services__heading::before,
  .services__heading::after {
    content: "";
    flex: 1;
    height: 1px;
    background: var(--white);
  }
  .services__list {
    margin-top: 10px;
    font-size: 19px;
    line-height: 25px;
    white-space: nowrap;
  }
</style>
</head>
<body>
  <section class="card card--front">
    <div class="contact-panel">
      <div class="person">
        <div class="person__name">Derek Holloway</div>
        <div class="person__phone">0407385510</div>
      </div>
      <div class="person">
        <div class="person__name">Megan Holloway</div>
        <div class="person__phone">0407913847</div>
      </div>
      <ul class="links">
        <li class="links__item">
          <svg class="links__icon" viewBox="0 0 17 17" aria-hidden="true">
            <rect x="1" y="3" width="15" height="11" fill="#1a7ac0"/>
            <path d="M1 3 L8.5 9.5 L16 3" fill="none" stroke="#2f2f2f" stroke-width="1.4"/>
          </svg>
          norrelladvisorywa@mailbox-example.com
        </li>
        <li class="links__item">
          <svg class="links__icon" viewBox="0 0 17 17" aria-hidden="true">
            <circle cx="8.5" cy="8.5" r="7.5" fill="#1a7ac0"/>
            <ellipse cx="8.5" cy="8.5" rx="3" ry="7.5" fill="none" stroke="#2f2f2f" stroke-width="1"/>
            <line x1="1" y1="8.5" x2="16" y2="8.5" stroke="#2f2f2f" stroke-width="1"/>
          </svg>
          www.norrelladvisorywa.example
        </li>
        <li class="links__item">
          <svg class="links__icon" viewBox="0 0 17 17" aria-hidden="true">
            <rect x="1.5" y="1.5" width="14" height="14" fill="#1a7ac0"/>
          </svg>
          norrelladvisorywa
        </li>
      </ul>
    </div>
    <div class="brand-panel">
      <div class="brand-panel__backdrop" role="img" aria-label="Soft pastel tiled puzzle-piece background pattern"></div>
      <div class="brand">
        <span class="brand__mark"></span>
        <div class="brand__name">Norrell Advisory</div>
        <div class="brand__tagline">Steady Steps Lasting Gains</div>
      </div>
    </div>
  </section>

  <section class="card card--back">
    <div class="back-brand">
      <span class="back-brand__mark"></span>
      <div class="back-brand__name">Norrell Advisory</div>
    </div>
    <div class="services">
      <h2 class="services__heading">Providing assistance with</h2>
      <p class="services__list">
        Organisation &amp; Efficiency • Revenue generation &amp; Marketing • Financial Management<br>
        Production quality &amp; delivery • Systems &amp; Process documentation • Exit Strategy
      </p>
    </div>
  </section>
</body>
</html>
```